Gooey Tides

I am creating an online slime shop that will sell handmade custom slimes. I need to be able to have payment/shipping options and the ability to change product photos since the product and product name will change often

Target Market(s)

Slime

Industry/Entity Type

Retail - online sales

Coding

Coded - Design and coding required

Number of Pages Required

2 page

Font styles to use
Sans Serif

Colors
0094D4
00A9DD
6FCCEA
C7EBF8
E9F6FB
E54698
E96AAD
F1A4CE
F9D9EA
FCEFF6
A7469A
B969AE
D3A5CF
EDDBEB
F8F0F9

Requirements
Must have
• My logo, my domain, ability to change photos of products for sale, payment options, shipping options, social media links, contact us,

```html
<!DOCTYPE html>
<html lang="en">
<head>
<meta charset="utf-8">
<title>Gooey Tides — Handmade Custom Slimes</title>
<link href="https://fonts.googleapis.com/css2?family=Open+Sans:wght@400;600;700;800&display=swap" rel="stylesheet">
<style>
:root{
  --blue:#0094D4;
  --blue-light:#00A9DD;
  --pink:#E5467F;
  --pink-btn:#C9407F;
  --pink-soft:#F1A4CE;
  --purple:#7B2BD1;
  --purple-deep:#8E2BD6;
  --violet:#A7469A;
  --ink:#111;
  --grey:#444;
  --white:#fff;
}
*{box-sizing:border-box;margin:0;padding:0}
html,body{width:1200px;height:2667px;overflow:hidden}
body{position:relative;background:var(--white);font-family:"Open Sans",sans-serif;color:var(--ink)}
.abs{position:absolute}
.topbar{left:0;top:0;width:1200px;height:35px;background:var(--blue);color:var(--white);font-size:12px;display:flex;align-items:center;justify-content:center;gap:10px}
.header{left:0;top:35px;width:1200px;height:90px;background:var(--white)}
.brand{left:112px;top:28px;display:flex;align-items:center;gap:8px;font-size:20px;font-weight:800;color:var(--violet)}
.brand-dot{width:22px;height:22px;border-radius:50%;background:var(--violet)}
.nav{left:272px;top:36px;display:flex;gap:0;font-size:15px;font-weight:600;color:var(--ink)}
.nav a{color:inherit;text-decoration:none;margin-right:54px;position:relative}
.nav a.active::after{content:"";position:absolute;left:2px;right:2px;bottom:-9px;height:2px;background:var(--blue)}
.nav-divider{left:866px;top:24px;width:1px;height:42px;background:#ccc}
.icon-btn{width:34px;height:34px;border:1.5px solid #333;border-radius:50%;display:flex;align-items:center;justify-content:center}
.cart{left:1008px;top:30px;display:flex;align-items:center;gap:8px;font-size:11px;line-height:1.4}
.hero{left:0;top:125px;width:1200px;height:471px;overflow:hidden}
.hero-photo{position:absolute;inset:0;background:linear-gradient(100deg,#b97a5a 0%,#d8b58a 45%,#c89a6a 70%,#8a5e3a 100%)}
.hero-panel{position:absolute;inset:0;background:linear-gradient(180deg,#8A24D8 0%,#B43AB0 50%,#E0467F 100%);clip-path:polygon(0 0,600px 0,515px 471px,0 471px);opacity:.96}
.hero h1{position:absolute;left:105px;top:94px;font-size:64px;font-weight:800;color:var(--white);letter-spacing:1px;line-height:1}
.hero h2{position:absolute;left:105px;top:168px;font-size:44px;font-weight:800;color:var(--white);line-height:1}
.hero p{position:absolute;left:107px;top:225px;width:370px;font-size:16px;line-height:28px;color:var(--white)}
.btn{display:inline-flex;align-items:center;justify-content:center;border-radius:22px;font-weight:700;text-decoration:none}
.hero .btn{position:absolute;left:107px;top:323px;width:202px;height:43px;background:var(--white);color:var(--purple);font-size:16px}
.feature{top:675px;width:230px;text-align:center;font-size:16px;line-height:24px;color:var(--grey)}
.feature svg{display:block;margin:0 auto 14px}
.section-title{left:0;width:1200px;text-align:center;font-size:42px;font-weight:800;letter-spacing:.5px}
.card{top:928px;width:230px;height:397px;background:var(--white);border-radius:6px;box-shadow:0 2px 14px rgba(0,0,0,.08);text-align:center}
.card-photo{margin:12px auto 0;width:206px;height:176px;border-radius:4px}
.actions{display:flex;justify-content:center;gap:8px;margin-top:22px}
.round{width:27px;height:27px;border-radius:50%;background:var(--pink-btn);display:flex;align-items:center;justify-content:center}
.round.on{background:var(--purple)}
.card h3,.arch-item h3{font-size:16px;font-weight:700;margin-top:10px}
.price{color:var(--purple);font-weight:700;font-size:16px;margin-top:6px}
.stars{font-size:16px;margin-top:4px}
.card .btn{margin-top:8px;width:110px;height:33px;background:var(--pink-btn);color:var(--white);font-size:14px}
.card .btn.on{background:var(--purple)}
.arrow{width:24px;height:24px}
.about{left:0;top:1408px;width:1200px;height:471px;overflow:hidden}
.about-photo{position:absolute;inset:0;background:linear-gradient(90deg,#d9b8a4 0%,#8a5a70 35%,#c9cdd8 60%,#dfe3ea 100%)}
.about-text{position:absolute;right:112px;top:98px;width:420px;text-align:right}
.about-text h2{font-size:42px;font-weight:800}
.about-text p{font-size:15.5px;line-height:29px;color:#222;margin-top:14px}
.about-text .btn{margin-top:24px;width:142px;height:43px;background:var(--purple);color:var(--white);font-size:16px}
.arch-item{top:2004px;width:230px;text-align:center}
.arch{width:230px;height:233px;border-radius:115px 115px 0 0}
.arch-item .actions{margin-top:52px}
.footer{left:0;top:2418px;width:1200px;height:249px;background:var(--blue);color:var(--white)}
.footer-brand{position:absolute;left:115px;top:90px;display:flex;align-items:center;gap:10px;font-size:28px;font-weight:800}
.footer-brand span.dot{width:30px;height:30px;border-radius:50%;background:var(--white)}
.copy{position:absolute;left:115px;top:196px;font-size:14px}
.footer h4{font-size:19px;font-weight:700;margin-bottom:20px}
.col{position:absolute;top:48px}
.col ul{list-style:none;font-size:15px;line-height:29px}
.contact-row{display:flex;gap:22px;font-size:15.5px;line-height:26px;margin-bottom:14px}
.contact-row svg{flex:none;margin-top:4px}
</style>
</head>
<body>

<div class="abs topbar"><span>***</span><span>At vero eos et accusamus et iusto odio dignissimos ducimus qui blanditiis praesentium voluptatum</span><span>***</span></div>

<header class="abs header">
  <div class="abs brand"><span class="brand-dot"></span>Gooey Tides</div>
  <nav class="abs nav">
    <a class="active" href="#">HOME</a><a href="#">ABOUT US</a><a href="#">SHOP</a><a href="#">CATEGORIES</a><a href="#">CONTACT US</a>
  </nav>
  <div class="abs nav-divider"></div>
  <div class="abs icon-btn" style="left:888px;top:28px"><svg width="14" height="14" viewBox="0 0 14 14" fill="none" stroke="#333" stroke-width="1.3"><circle cx="7" cy="4.5" r="2.8"/><path d="M2 13c0-3 2.2-4.5 5-4.5s5 1.5 5 4.5z"/></svg></div>
  <div class="abs icon-btn" style="left:939px;top:28px"><svg width="15" height="14" viewBox="0 0 16 14" fill="none" stroke="#333" stroke-width="1.3"><path d="M8 13S1 8.6 1 4.5A3.4 3.4 0 0 1 8 3a3.4 3.4 0 0 1 7 1.5C15 8.6 8 13 8 13z"/></svg></div>
  <div class="abs cart">
    <svg width="24" height="30" viewBox="0 0 24 30"><path d="M7 9V6a5 5 0 0 1 10 0v3" fill="none" stroke="#000" stroke-width="2"/><rect x="1" y="9" width="22" height="20" rx="3" fill="#000"/></svg>
    <div>(2)<br>MY CART</div>
  </div>
</header>

<section class="abs hero">
  <div class="hero-photo" role="img" aria-label="Photo of children stretching pink slime at a play table"></div>
  <div class="hero-panel"></div>
  <h1>HANDMADE</h1>
  <h2>CUSTOM SLIMES</h2>
  <p>At vero eos et accusamus et iusto odio dignissimos ducimus qui blanditiis praesentium voluptatum</p>
  <a class="btn" href="#">Shop Our Products</a>
</section>

<div class="abs feature" style="left:96px">
  <svg width="56" height="50" viewBox="0 0 56 50"><circle cx="34" cy="26" r="20" fill="#F9D9EA"/><circle cx="25" cy="23" r="18" fill="none" stroke="#A7469A" stroke-width="2"/><circle cx="25" cy="23" r="11" fill="none" stroke="#A7469A" stroke-width="2"/><path d="M20 23l4 4 7-8" fill="none" stroke="#A7469A" stroke-width="2"/></svg>
  At vero eos et accusamus et iusto odio dig
</div>
<div class="abs feature" style="left:363px">
  <svg width="56" height="50" viewBox="0 0 56 50"><circle cx="34" cy="26" r="20" fill="#F9D9EA"/><circle cx="25" cy="23" r="18" fill="none" stroke="#A7469A" stroke-width="2" stroke-dasharray="90 20"/><text x="25" y="28" font-family="Open Sans,sans-serif" font-size="12" font-weight="700" fill="#A7469A" text-anchor="middle">24/7</text></svg>
  At vero eos et accusamus et iusto odio dig
</div>
<div class="abs feature" style="left:629px">
  <svg width="56" height="50" viewBox="0 0 56 50"><circle cx="34" cy="26" r="20" fill="#F9D9EA"/><path d="M8 14l17-8 17 8v20l-17 8-17-8z M8 14l17 8 17-8 M25 22v20" fill="none" stroke="#A7469A" stroke-width="2" stroke-linejoin="round"/></svg>
  At vero eos et accusamus et iusto odio dig
</div>
<div class="abs feature" style="left:896px">
  <svg width="56" height="50" viewBox="0 0 56 50"><circle cx="34" cy="26" r="20" fill="#F9D9EA"/><path d="M25 4l5 11 12 1-9 8 3 12-11-6-11 6 3-12-9-8 12-1z" fill="none" stroke="#A7469A" stroke-width="2" stroke-linejoin="round"/></svg>
  At vero eos et accusamus et iusto odio dig
</div>

<h2 class="abs section-title" style="top:852px">SHOP OUR PRODUCTS</h2>

<svg class="abs arrow" style="left:47px;top:1114px" viewBox="0 0 24 24"><circle cx="12" cy="12" r="10.5" fill="none" stroke="#bbb" stroke-width="2"/><path d="M17 12H8m3-4l-4 4 4 4" fill="none" stroke="#bbb" stroke-width="2"/></svg>
<svg class="abs arrow" style="left:1126px;top:1114px" viewBox="0 0 24 24"><circle cx="12" cy="12" r="10.5" fill="none" stroke="#555" stroke-width="2"/><path d="M7 12h9m-3-4l4 4-4 4" fill="none" stroke="#555" stroke-width="2"/></svg>

<div class="abs card" style="left:112px">
  <div class="card-photo" role="img" aria-label="Product photo of a glittery pastel slime jar" style="background:linear-gradient(160deg,#f27c8c,#e6c08a 60%,#7fd0d8)"></div>
  <div class="actions"><span class="round"><svg width="13" height="9" viewBox="0 0 14 10"><path d="M1 5s2.5-4 6-4 6 4 6 4-2.5 4-6 4-6-4-6-4z" fill="#fff"/><circle cx="7" cy="5" r="1.8" fill="#C9407F"/></svg></span><span class="round"><svg width="11" height="10" viewBox="0 0 16 14"><path d="M8 13S1 8.6 1 4.5A3.4 3.4 0 0 1 8 3a3.4 3.4 0 0 1 7 1.5C15 8.6 8 13 8 13z" fill="#fff"/></svg></span></div>
  <h3>FLUFFY BUTTER SLIME</h3><div class="price">$ 16.99</div><div class="stars">★★★★☆ &nbsp;(125)</div>
  <a class="btn" href="#">Buy Now</a>
</div>
<div class="abs card" style="left:360px">
  <div class="card-photo" role="img" aria-label="Product photo of a silver sequin slime jar" style="background:linear-gradient(160deg,#6d5a70,#b9c0c8 55%,#4a6a78)"></div>
  <div class="actions"><span class="round"><svg width="13" height="9" viewBox="0 0 14 10"><path d="M1 5s2.5-4 6-4 6 4 6 4-2.5 4-6 4-6-4-6-4z" fill="#fff"/><circle cx="7" cy="5" r="1.8" fill="#C9407F"/></svg></span><span class="round"><svg width="11" height="10" viewBox="0 0 16 14"><path d="M8 13S1 8.6 1 4.5A3.4 3.4 0 0 1 8 3a3.4 3.4 0 0 1 7 1.5C15 8.6 8 13 8 13z" fill="#fff"/></svg></span></div>
  <h3>FLUFFY BUTTER SLIME</h3><div class="price">$ 16.99</div><div class="stars">★★★★☆ &nbsp;(125)</div>
  <a class="btn on" href="#">Buy Now</a>
</div>
<div class="abs card" style="left:609px">
  <div class="card-photo" role="img" aria-label="Product photo of a green garden scene slime" style="background:linear-gradient(170deg,#6f7070,#5d8a3a 50%,#6fd4b0)"></div>
  <div class="actions"><span class="round"><svg width="13" height="9" viewBox="0 0 14 10"><path d="M1 5s2.5-4 6-4 6 4 6 4-2.5 4-6 4-6-4-6-4z" fill="#fff"/><circle cx="7" cy="5" r="1.8" fill="#C9407F"/></svg></span><span class="round"><svg width="11" height="10" viewBox="0 0 16 14"><path d="M8 13S1 8.6 1 4.5A3.4 3.4 0 0 1 8 3a3.4 3.4 0 0 1 7 1.5C15 8.6 8 13 8 13z" fill="#fff"/></svg></span></div>
  <h3>FLUFFY BUTTER SLIME</h3><div class="price">$ 16.99</div><div class="stars">★★★★☆ &nbsp;(125)</div>
  <a class="btn" href="#">Buy Now</a>
</div>
<div class="abs card" style="left:858px">
  <div class="card-photo" role="img" aria-label="Product photo of a pink waffle topped slime jar" style="background:linear-gradient(170deg,#8a7a70,#f0a0b0 50%,#e070c0)"></div>
  <div class="actions"><span class="round"><svg width="13" height="9" viewBox="0 0 14 10"><path d="M1 5s2.5-4 6-4 6 4 6 4-2.5 4-6 4-6-4-6-4z" fill="#fff"/><circle cx="7" cy="5" r="1.8" fill="#C9407F"/></svg></span><span class="round"><svg width="11" height="10" viewBox="0 0 16 14"><path d="M8 13S1 8.6 1 4.5A3.4 3.4 0 0 1 8 3a3.4 3.4 0 0 1 7 1.5C15 8.6 8 13 8 13z" fill="#fff"/></svg></span></div>
  <h3>FLUFFY BUTTER SLIME</h3><div class="price">$ 16.99</div><div class="stars">★★★★☆ &nbsp;(125)</div>
  <a class="btn" href="#">Buy Now</a>
</div>

<section class="abs about">
  <div class="about-photo" role="img" aria-label="Photo of a smiling child and a teacher playing together in a classroom"></div>
  <div class="about-text">
    <h2>ABOUT US</h2>
    <p>Sed ut perspiciatis unde omnis iste natus error sit voluptatem accusantium doloremque laudantium, totam rem aperiam, eaque ipsa quae ab illo inventore veritatis et quasi architecto beatae vitae dicta sunt explicabo. Nemo enim ipsam voluptatem quia voluptas</p>
    <a class="btn" href="#">Read More</a>
  </div>
</section>

<h2 class="abs section-title" style="top:1927px">BEST-SELLING SLIMES</h2>

<svg class="abs arrow" style="left:47px;top:2214px" viewBox="0 0 24 24"><circle cx="12" cy="12" r="10.5" fill="none" stroke="#bbb" stroke-width="2"/><path d="M17 12H8m3-4l-4 4 4 4" fill="none" stroke="#bbb" stroke-width="2"/></svg>
<svg class="abs arrow" style="left:1126px;top:2214px" viewBox="0 0 24 24"><circle cx="12" cy="12" r="10.5" fill="none" stroke="#555" stroke-width="2"/><path d="M7 12h9m-3-4l4 4-4 4" fill="none" stroke="#555" stroke-width="2"/></svg>

<div class="abs arch-item" style="left:112px">
  <div class="arch" role="img" aria-label="Product photo of a purple slime jar" style="background:radial-gradient(circle at 50% 60%,#b01ad0 0 32%,#6a1470 33%,#8a1a6a 100%)"></div>
  <div class="actions"><span class="round"><svg width="13" height="9" viewBox="0 0 14 10"><path d="M1 5s2.5-4 6-4 6 4 6 4-2.5 4-6 4-6-4-6-4z" fill="#fff"/><circle cx="7" cy="5" r="1.8" fill="#C9407F"/></svg></span><span class="round"><svg width="11" height="10" viewBox="0 0 16 14"><path d="M8 13S1 8.6 1 4.5A3.4 3.4 0 0 1 8 3a3.4 3.4 0 0 1 7 1.5C15 8.6 8 13 8 13z" fill="#fff"/></svg></span></div>
  <h3>FLUFFY BUTTER SLIME</h3>
</div>
<div class="abs arch-item" style="left:360px">
  <div class="arch" role="img" aria-label="Product photo of a red slime jar" style="background:radial-gradient(circle at 50% 60%,#d01030 0 32%,#7a1a30 33%,#9a1a4a 100%)"></div>
  <div class="actions"><span class="round"><svg width="13" height="9" viewBox="0 0 14 10"><path d="M1 5s2.5-4 6-4 6 4 6 4-2.5 4-6 4-6-4-6-4z" fill="#fff"/><circle cx="7" cy="5" r="1.8" fill="#C9407F"/></svg></span><span class="round on"><svg width="11" height="10" viewBox="0 0 16 14"><path d="M8 13S1 8.6 1 4.5A3.4 3.4 0 0 1 8 3a3.4 3.4 0 0 1 7 1.5C15 8.6 8 13 8 13z" fill="#fff"/></svg></span></div>
  <h3>FLUFFY BUTTER SLIME</h3>
</div>
<div class="abs arch-item" style="left:609px">
  <div class="arch" role="img" aria-label="Product photo of a blue slime jar" style="background:radial-gradient(circle at 50% 60%,#1a8ae0 0 32%,#2a4a80 33%,#6a2a70 100%)"></div>
  <div class="actions"><span class="round"><svg width="13" height="9" viewBox="0 0 14 10"><path d="M1 5s2.5-4 6-4 6 4 6 4-2.5 4-6 4-6-4-6-4z" fill="#fff"/><circle cx="7" cy="5" r="1.8" fill="#C9407F"/></svg></span><span class="round"><svg width="11" height="10" viewBox="0 0 16 14"><path d="M8 13S1 8.6 1 4.5A3.4 3.4 0 0 1 8 3a3.4 3.4 0 0 1 7 1.5C15 8.6 8 13 8 13z" fill="#fff"/></svg></span></div>
  <h3>FLUFFY BUTTER SLIME</h3>
</div>
<div class="abs arch-item" style="left:858px">
  <div class="arch" role="img" aria-label="Product photo of an orange slime jar" style="background:radial-gradient(circle at 50% 60%,#f07a10 0 32%,#7a2a20 33%,#9a1a3a 100%)"></div>
  <div class="actions"><span class="round"><svg width="13" height="9" viewBox="0 0 14 10"><path d="M1 5s2.5-4 6-4 6 4 6 4-2.5 4-6 4-6-4-6-4z" fill="#fff"/><circle cx="7" cy="5" r="1.8" fill="#C9407F"/></svg></span><span class="round"><svg width="11" height="10" viewBox="0 0 16 14"><path d="M8 13S1 8.6 1 4.5A3.4 3.4 0 0 1 8 3a3.4 3.4 0 0 1 7 1.5C15 8.6 8 13 8 13z" fill="#fff"/></svg></span></div>
  <h3>FLUFFY BUTTER SLIME</h3>
</div>

<footer class="abs footer">
  <div class="footer-brand"><span class="dot"></span>Gooey Tides</div>
  <div class="copy">(C) Copyright 2024 | All Rights Reserved</div>

  <div class="col" style="left:468px">
    <h4>CONTACT US</h4>
    <div class="contact-row"><svg width="16" height="20" viewBox="0 0 16 20"><path d="M8 0a7 7 0 0 0-7 7c0 5 7 13 7 13s7-8 7-13a7 7 0 0 0-7-7z" fill="#fff"/><circle cx="8" cy="7" r="2.6" fill="#0094D4"/></svg><span>Gooey Tides,<br>Alabama, USA</span></div>
    <div class="contact-row"><svg width="16" height="16" viewBox="0 0 16 16"><path d="M3 1l3 3-2 2a10 10 0 0 0 6 6l2-2 3 3-2 2C7 15 1 9 1 3z" fill="#fff"/></svg><span>555-014-2298</span></div>
    <div class="contact-row"><svg width="16" height="12" viewBox="0 0 16 12"><rect width="16" height="12" rx="1" fill="#fff"/><path d="M0 1l8 6 8-6" fill="none" stroke="#0094D4" stroke-width="1.5"/></svg><span>hello@gooeytides.shop</span></div>
  </div>
  <div class="col" style="left:783px">
    <h4>QUICK LINKS</h4>
    <ul><li>Home</li><li>About Us</li><li>Products</li><li>Reviews</li></ul>
  </div>
  <div class="col" style="left:974px">
    <h4>HELP LINKS</h4>
    <ul><li>Help</li><li>SitemapTerms</li><li>Privacy Policy</li><li>Contact Us</li></ul>
  </div>
</footer>

</body>
</html>
```